Thornbury Spa

We are a large Miami Beach spa and salon. I am still building our website but you can use it as a resource to gain a better understanding of who we are ....www.velloraspa-studio.com.

We offer a comprehensive list of services in hair, nails, massage, skin care, tanning, spray tanning and waxing and we offer high quality products for skin care, tanning and hair. We are open 7 days.

We would like to see a clean and simple menu that looks a lot like the one from "The Spa at Larkwood." In particular, we have a copy of a menu from their West Hollywood, CA location that is just beautiful. In the uploaded content you will see a sampling of that menu. We would like to see greys, blacks, silvers, whites and warm colors like reds and oranges. We specifically attempt to remain gender neutral so that we don't attract only girls (with pink colors and flowers etc). The final design should convey a simple, clean, friendly environment and the final product should be sized such that it is 1.) portable and 2.) inexpensive to print. We will be running thousands of these at a time so cost of printing is a consideration.

The booklet consists of two parts: one part is the standard menu with descriptions of services and products and photos etc (think of this as the sales piece that convinces a potential customer to visit) and will be stapled together like you would expect a small menu to be and should resemble the Larkwood menu. The prices should not be included in this part of the booklet that will be printed and stapled. The other part is a single insert and is removable and replaceable. I want this removable insert placed in the last page of the book in a folder pocket or something else that you can think of so that when it's time to change prices here that I am not throwing away all of the booklets....I am only replacing the inserts at the end of the menu booklet. Please design this single page insert so that should a customer remove it from the booklet and keep it, that it stands alone with our name, logo, website and phone number. This page can and probably will have to be 2 sided.

At the back of the booklet, I also want the polices to be printed in one page (think fine print in any sort of business dealing.)

With regard to the look and feel slider of economical v upmarket...we definitely want to convey we deliver upmarket services at reasonable prices. Think, world class services and products at reasonable, everyday prices.

With regard to the uploaded files:
I uploaded both EPS and TIF formats. The colors in those files are not the palette we want at all. The colors we want use for the circular logo must match the standard colors as depicted in the uploaded file "Thornburytanrooms"

Target Market(s)

The target market is the average 20-35 year old in Miami Beach that cares about their appearance. The range of clientele is quite diverse.

Industry/Entity Type

Environment

Requirements
Must have
• It must have elegant and simple photographs that relate to the services being offered. We are selling a service set and an environment...so this menu should be reflect that goal. The logo should be repeated often throughout the book but in subtle ways.

Stock photos are fine as long as they don't seem obviously stock.

Should not have
• Nothing buddha like. Nothing themed. It should be all inclusive and not seek to identify with any particular group or gender.

Nothing that fits the stereotype of "Miami Beach." We want to represent ourselves in the same category as the best spas in the world because we moving everything we do in that direction. Think class!

```html
<!DOCTYPE html>
<html lang="en">
<head>
<meta charset="utf-8">
<title>Thornbury Spa — Hair &amp; Nails Menu</title>
<link href="https://fonts.googleapis.com/css2?family=Jost:wght@300;400&family=Open+Sans:wght@400&display=swap" rel="stylesheet">
<style>
  :root {
    --canvas: #e9e9e9;
    --numeral: #b9b9b9;
    --panel-dark: #232121;
    --panel-mid: #4b4848;
    --bar-grey: #8d8d8d;
    --bar-grey-light: #a7a7a7;
    --tab-grey: #9c9c9c;
    --tab-text: #2b2b2b;
    --body-text: #d8d6d6;
    --white: #ffffff;
    --terracotta: #c4705a;
    --lilac: #9a7a98;
    --hair-deep: #3a1a12;
    --hair-warm: #9c4128;
    --skin: #d9a28a;
    --salon-light: #f2e6ec;
    --salon-pink: #d9b8d4;
    --salon-floor: #c7a893;
  }
  * { box-sizing: border-box; margin: 0; padding: 0; }
  html, body { width: 1200px; height: 900px; overflow: hidden; }
  body {
    position: relative;
    background: var(--canvas);
    font-family: "Open Sans", Arial, sans-serif;
  }
  .page-number {
    position: absolute;
    font-family: "Jost", sans-serif;
    font-weight: 300;
    font-size: 30px;
    color: var(--numeral);
    letter-spacing: 2px;
  }
  .spread {
    position: absolute;
    left: 103px;
    width: 1002px;
    height: 352px;
    overflow: hidden;
    background: radial-gradient(ellipse at 65% 45%, var(--panel-mid) 0%, var(--panel-dark) 75%);
    box-shadow: 2px 4px 8px rgba(0,0,0,0.35);
  }
  .spread--hair { top: 62px; }
  .spread--nails { top: 483px; }
  .spread__shapes { position: absolute; inset: 0; }
  .spread__watermark {
    position: absolute;
    left: 14px;
    top: -8px;
    font-family: "Jost", sans-serif;
    font-weight: 300;
    font-size: 112px;
    line-height: 1;
    letter-spacing: 2px;
    color: rgba(255,255,255,0.45);
  }
  .spread--nails .spread__watermark { font-size: 116px; color: rgba(255,255,255,0.7); left: 12px; top: -6px; }
  .menu-title {
    position: absolute;
    right: 34px;
    top: 14px;
    font-family: "Jost", sans-serif;
    font-weight: 400;
    font-size: 46px;
    line-height: 1;
    color: var(--white);
    letter-spacing: 0.5px;
  }
  .brand {
    position: absolute;
    display: flex;
    flex-direction: column;
    align-items: center;
    gap: 4px;
    font-family: "Jost", sans-serif;
    font-weight: 400;
    font-size: 9px;
    letter-spacing: 1px;
    color: var(--bar-grey-light);
    text-transform: uppercase;
  }
  .brand__dot {
    width: 16px; height: 16px;
    border-radius: 50%;
    border: 1px solid var(--bar-grey-light);
  }
  .service {
    position: absolute;
    width: 132px;
  }
  .service__tab {
    display: block;
    height: 10px;
    background: var(--tab-grey);
    font-family: "Jost", sans-serif;
    font-size: 8.5px;
    line-height: 10px;
    letter-spacing: 1px;
    text-align: center;
    text-transform: uppercase;
    color: var(--tab-text);
    margin-bottom: 5px;
  }
  .service__list { list-style: none; }
  .service__list li {
    font-size: 6.6px;
    line-height: 8.6px;
    color: var(--body-text);
  }
  .service--wide { width: 212px; }
  .service--wide .service__tab { width: 134px; }
  .service__desc {
    font-size: 6.1px;
    line-height: 8.6px;
    color: var(--body-text);
    text-align: justify;
  }
</style>
</head>
<body>

  <span class="page-number" style="left:38px; top:228px;">1.</span>
  <span class="page-number" style="left:1138px; top:228px;">2.</span>
  <span class="page-number" style="left:38px; top:640px;">3.</span>
  <span class="page-number" style="left:1138px; top:640px;">4.</span>

  <!-- Hair spread -->
  <section class="spread spread--hair" aria-label="Hair menu">
    <svg class="spread__shapes" width="1002" height="352" viewBox="0 0 1002 352">
      <defs>
        <linearGradient id="hairPhoto" x1="0" y1="0" x2="1" y2="1">
          <stop offset="0" stop-color="var(--hair-warm)"/>
          <stop offset="0.45" stop-color="var(--skin)"/>
          <stop offset="0.8" stop-color="var(--hair-warm)"/>
          <stop offset="1" stop-color="var(--hair-deep)"/>
        </linearGradient>
        <linearGradient id="hairBar" x1="0" y1="0" x2="1" y2="0">
          <stop offset="0" stop-color="#6e6c6c"/>
          <stop offset="1" stop-color="var(--bar-grey-light)"/>
        </linearGradient>
      </defs>
      <polygon points="0,0 410,0 482,352 0,352" fill="url(#hairPhoto)" role="img" aria-label="Photograph of a woman with long auburn hair resting her head"/>
      <polygon points="410,0 465,0 530,352 482,352" fill="var(--terracotta)"/>
      <polygon points="458,18 1002,18 1002,56 466,56" fill="url(#hairBar)"/>
      <circle cx="935" cy="288" r="58" fill="none" stroke="#5a5757" stroke-width="4"/>
    </svg>
    <div class="spread__watermark">HAIR</div>
    <h1 class="menu-title">HAIR MENU</h1>
    <div class="brand" style="left:528px; top:95px;"><span class="brand__dot"></span>Thornbury Spa</div>

    <div class="service" style="left:642px; top:98px;">
      <span class="service__tab">Cutting</span>
      <ul class="service__list">
        <li>men's hair cut/trim</li>
        <li>women's wet cut/trim</li>
        <li>women's cut &amp; blowout</li>
      </ul>
    </div>
    <div class="service" style="left:642px; top:170px;">
      <span class="service__tab">Styling</span>
      <ul class="service__list">
        <li>wet head blowout</li>
        <li>shampoo &amp; blowout</li>
        <li>updos or styling</li>
        <li>wedding hair trials</li>
        <li>wedding day hair</li>
      </ul>
    </div>
    <div class="service" style="left:642px; top:251px;">
      <span class="service__tab">Treatments</span>
      <ul class="service__list">
        <li>scalp massage + nourishing treatment</li>
        <li>ultra conditioning reconstructor</li>
        <li>keratin by corvella treatment</li>
      </ul>
    </div>
    <div class="service" style="left:798px; top:98px;">
      <span class="service__tab">Extensions</span>
      <ul class="service__list">
        <li>hair extensions by lumenlocks</li>
        <li>extensions repair</li>
        <li>extensions removal</li>
      </ul>
    </div>
    <div class="service" style="left:798px; top:170px;">
      <span class="service__tab">Coloring</span>
      <ul class="service__list">
        <li>single process</li>
        <li>partial highlights/lowlights</li>
        <li>full highlights/lowlights</li>
        <li>double process</li>
      </ul>
    </div>
  </section>

  <!-- Nails spread -->
  <section class="spread spread--nails" aria-label="Nails menu">
    <svg class="spread__shapes" width="1002" height="352" viewBox="0 0 1002 352">
      <defs>
        <linearGradient id="nailsPhoto" x1="0" y1="0" x2="0" y2="1">
          <stop offset="0" stop-color="var(--salon-pink)"/>
          <stop offset="0.4" stop-color="var(--salon-light)"/>
          <stop offset="0.8" stop-color="#e8dcd4"/>
          <stop offset="1" stop-color="var(--salon-floor)"/>
        </linearGradient>
        <linearGradient id="nailsBar" x1="0" y1="0" x2="1" y2="0">
          <stop offset="0" stop-color="#6e6c6c"/>
          <stop offset="1" stop-color="var(--bar-grey-light)"/>
        </linearGradient>
      </defs>
      <polygon points="0,0 292,0 384,352 0,352" fill="url(#nailsPhoto)" role="img" aria-label="Photograph of a bright salon with white pedicure chairs and soft purple lighting"/>
      <polygon points="292,0 327,0 407,352 384,352" fill="var(--lilac)"/>
      <polygon points="322,20 1002,20 1002,57 331,57" fill="url(#nailsBar)"/>
    </svg>
    <div class="spread__watermark">NAILS</div>
    <h1 class="menu-title" style="top:16px;">NAILS MENU</h1>
    <div class="brand" style="left:392px; top:104px;"><span class="brand__dot"></span>Thornbury Spa</div>

    <div class="service service--wide" style="left:530px; top:81px;">
      <span class="service__tab">The Classic</span>
      <p class="service__desc">Our Classic option is just what your nails need on a regular basis. We start with a purifying and thorough soak to soften your nails and cuticles. We then follow with an aromatic, exfoliating massage of the hands and the feet, designed to smooth and soften your hands and feet. We remove your existing laquer, groom and oil your cuticles, shape and buff your nails and finish with the application of your favorite nail lacquer.</p>
    </div>
    <div class="service service--wide" style="left:530px; top:166px;">
      <span class="service__tab">Gelvara</span>
      <p class="service__desc">For those who get caught up and go too long between visits, we definitely suggest Gelvara. This unique polish is resistant to chipping, maintains an incredible shine and can last up to 21 days. We begin this option with a purifying and thorough soak to soften your nails and cuticles. We follow with an aromatic, exfoliating massage of the hands and the feet, designed to smooth and soften your hands or feet. We remove your existing laquer, groom and oil your cuticles, shape your nails and finish with your chosen Gelvara colors.</p>
    </div>
    <div class="service service--wide" style="left:530px; top:268px;">
      <span class="service__tab">Natural Nail Overlays</span>
      <p class="service__desc">Use of natural nail overlays allows your nails to grow, prevent damage and maintain a beautiful look. Let our experienced and trained nail technicians recommend the overlay that fits your lifestyle, occupation and desired look.</p>
    </div>
    <div class="service service--wide" style="left:757px; top:81px;">
      <span class="service__tab">The Express</span>
      <p class="service__desc">If you are in a mad rush but absolutely need to pay a few minutes' attention to your hands and feet, we have the perfect option. We include just the essentials - removal of existing nail lacquer, a quick soak, cuticle grooming, nail shaping and the application of your favorite lacquer. This option will get you in and out in no time!</p>
    </div>
    <div class="service service--wide" style="left:757px; top:166px;">
      <span class="service__tab">The Ultimate</span>
      <p class="service__desc">If you want to give your hands and feet a little extra attention, you have to experience our spa treatment. Like our Classic treatment, we remove your existing polish, groom and oil your cuticles, shape and buff your nails and finish with the application of your favorite nail lacquer. From there, we massage your forearms and hands, calves and feet, incorporating warm towels and hot stones. We finish with a paraffin hand treatment, intended to leave your hands silky smooth, and we include chemical callus removal.</p>
    </div>
    <div class="service service--wide" style="left:757px; top:268px;">
      <span class="service__tab">Nail Bar Polishing</span>
      <p class="service__desc">Especially designed for those in a rush! We'll remove existing lacquer, apply a fresh coat of your favorite lacquer and you'll finish with a quick dry to get you on your way.</p>
    </div>
  </section>

</body>
</html>
```